International business needs business cards

Our company, DRV Ventures Inc. is in the business of supplying a range construction products with particular emphasis on CEMENT. We have developed our own brand - TORVAN SUPPLIES - with which to infiltrate the market. We are launching our brand of cement (TORVAN Type IS Cement) into the Caribbean which is unlike anything this market has ever seen. A monopoly has existed here for the past 60-odd years and the market has now opened to allow the importation of other brands and consumers are anxious and ready for change/improvement. We are very excited to be launching and want to make a great first impression. We will be conducting workshops and seminars (from government level to the hardware store owners) and we want our business card to give us the strong, confident introduction that we need.

Target Market(s)

construction; builders; engineers; home owners

Industry/Entity Type

Construction

Contact Information for Business Card

Marisol Depree
CEO
cell # 1 555 4180736
Ground floor,Lindell Plaza Suite 2734
George Town,Grand Cayman
Cayman Islands,KY1-4823
EMAIL: m.depree@drvventuresinc.example
web site drvventuresinc.example

COMPANY: skype info drv.ventures.example

second card
Yvette Brannock-Depree
CFO
CELL# 1 555 607 3941
George Town,Grand Cayman
Cayman Islands,KY1-4823
EMAIL: y.brannockdepree@drvventuresinc.example
website drvventuresinc.example

Requirements
Must have
• Business cards must display BOTH logos - DRV is the company and TORVAN is the brand.

```html
<!DOCTYPE html>
<html lang="en">
<head>
<meta charset="utf-8">
<title>DRV Ventures Inc. – Business Card</title>
<link rel="stylesheet" href="https://fonts.googleapis.com/css2?family=Open+Sans:wght@400;700&display=swap">
<style>
  :root {
    --backdrop: #4a423d;
    --card-black: #070707;
    --card-sheen: #262626;
    --brand-red: #8e1519;
    --text-white: #ffffff;
    --text-soft: #e6e6e6;
    --stripe-white: #f2f2f2;
  }
  * { box-sizing: border-box; margin: 0; padding: 0; }
  html, body {
    width: 1200px; height: 844px; overflow: hidden;
    background: var(--backdrop);
    font-family: "Open Sans", Arial, sans-serif;
  }
  .canvas {
    position: relative; width: 1200px; height: 844px;
    display: flex; align-items: center; justify-content: center; gap: 60px;
  }
  .card {
    position: relative; width: 510px; height: 292px;
    background: var(--card-black);
    overflow: hidden;
    box-shadow: 0 8px 22px rgba(0,0,0,.45);
  }

  /* Contact side */
  .card--contact {
    background: linear-gradient(160deg, var(--card-sheen) 0%, var(--card-black) 55%);
  }
  .band {
    position: absolute; left: 0; right: 0; height: 14px;
    background: var(--brand-red);
  }
  .band--top { top: 0; }
  .band--bottom { bottom: 0; }
  .contact {
    position: absolute; top: 44px; left: 150px; width: 300px;
    text-align: center; color: var(--text-soft);
    font-size: 13px; line-height: 18px;
  }
  .contact__name { color: var(--text-white); font-weight: 700; font-size: 17px; line-height: 22px; }
  .contact__role { font-size: 11px; margin-bottom: 24px; }
  .contact__address { margin-bottom: 26px; }
  .contact__line { display: flex; align-items: center; justify-content: center; gap: 6px; }
  .contact__line svg { width: 11px; height: 11px; fill: var(--text-white); flex: none; }

  /* Logo side */
  .card--brand {
    background: radial-gradient(ellipse at 48% 42%, #2b2b2b 0%, var(--card-black) 62%);
  }
  .tab {
    position: absolute; width: 26px; height: 34px; background: var(--brand-red);
  }
  .tab::after {
    content: ""; position: absolute; top: 0; bottom: 0; width: 4px; background: var(--stripe-white);
  }
  .tab--right { right: 0; top: 34px; }
  .tab--right::after { left: 4px; }
  .tab--left { left: 0; top: 190px; }
  .tab--left::after { right: 4px; }
  .company-mark {
    position: absolute; left: 110px; top: 82px;
    display: flex; align-items: center; gap: 14px;
  }
  .company-mark__square { width: 70px; height: 70px; background: var(--brand-red); }
  .company-mark__name {
    color: var(--text-white); font-weight: 700; font-size: 30px; line-height: 1; letter-spacing: .5px;
  }
  .product-mark {
    position: absolute; left: 230px; top: 176px;
    display: flex; align-items: center; gap: 8px;
  }
  .product-mark__circle { width: 22px; height: 22px; border-radius: 50%; background: #5a5a5a; }
  .product-mark__name { color: var(--text-white); font-weight: 700; font-size: 14px; letter-spacing: 1px; }
</style>
</head>
<body>
<main class="canvas">
  <section class="card card--contact" aria-label="Contact side">
    <div class="band band--top"></div>
    <div class="band band--bottom"></div>
    <div class="contact">
      <p class="contact__name">Marisol Depree</p>
      <p class="contact__role">CEO</p>
      <p class="contact__address">Ground floor, Lindell Plaza Suite 2734<br>George Town, Grand Cayman<br>Cayman Islands, KY1-4823</p>
      <p class="contact__line">
        <svg viewBox="0 0 16 16" aria-hidden="true"><path d="M3 1l3 3-1.6 2.2a9 9 0 0 0 5.4 5.4L12 10l3 3-2 2C6 15 1 10 1 3z"/></svg>
        1 555 4180736
      </p>
      <p class="contact__line">
        <svg viewBox="0 0 16 16" aria-hidden="true"><path d="M1 3h14v10H1z M1 3l7 6 7-6" stroke="#070707" stroke-width="1.2"/></svg>
        m.depree@drvventuresinc.example
      </p>
      <p class="contact__line">
        <svg viewBox="0 0 16 16" aria-hidden="true"><circle cx="8" cy="8" r="7"/><path d="M1 8h14M8 1c3 3 3 11 0 14M8 1c-3 3-3 11 0 14" stroke="#070707" stroke-width="1" fill="none"/></svg>
        www.drvventuresinc.example
      </p>
    </div>
  </section>

  <section class="card card--brand" aria-label="Brand side">
    <div class="tab tab--right"></div>
    <div class="tab tab--left"></div>
    <div class="company-mark">
      <div class="company-mark__square"></div>
      <p class="company-mark__name">DRV Ventures Inc.</p>
    </div>
    <div class="product-mark">
      <div class="product-mark__circle"></div>
      <p class="product-mark__name">TORVAN</p>
    </div>
  </section>
</main>
</body>
</html>
```